Interior design service, along with home organization, packing, and staging, home and business. As well as staging in conjunction with real estate sales.
Updates

Love many of your designs and will be choosing today. To inform you of the exact details needed, the name of the company is "Flourish by Marnie T" , my phone number and e-,ail need to be included. i also need either description or some sort of bullet points that give an idea of the following:

- Interior design for home and business
- Home organization and packing
- Staging for personal and professional space
- Real estate stagingĀ 

Thank you

Target Market(s)

wide audience, but most importantly people looking for a quality service

Industry/Entity Type

Real Estate

Contact Information for Business Card

Flourish By Marnie T
Marnie Tolvery
(555)687-3914
mtbrisco@postwell.example

Requirements
Must have
• I'm 29 so i want my card to reflect something professional but still fresh. I don't have any specific photos or quotes that Ive included, however I like the card to reflect a personal touch, which is what I'm seeking from this service in the design of my card. Thanks!

```html
<!DOCTYPE html>
<html lang="en">
<head>
<meta charset="utf-8">
<title>Flourish by Marnie T – Business Card</title>
<link rel="stylesheet" href="https://fonts.googleapis.com/css2?family=Marcellus&family=Tinos:wght@700&display=swap">
<style>
  :root {
    --backdrop: #d4d5d8;
    --card-black: #0b0b0c;
    --card-sheen: #1a1a1c;
    --accent-blue: #3f9fd8;
    --headline-white: #ffffff;
    --service-grey: #d8dadd;
  }
  * { margin: 0; padding: 0; box-sizing: border-box; }
  html, body {
    width: 1200px;
    height: 960px;
    overflow: hidden;
    background: var(--backdrop);
  }
  .canvas {
    position: relative;
    width: 1200px;
    height: 960px;
  }
  .card {
    position: absolute;
    width: 600px;
    height: 350px;
    overflow: hidden;
    background:
      repeating-linear-gradient(90deg, rgba(255,255,255,0.018) 0 2px, transparent 2px 7px),
      linear-gradient(90deg, var(--card-black) 0%, var(--card-sheen) 35%, var(--card-black) 70%, var(--card-sheen) 100%);
  }
  .card-front { left: 80px; top: 29px; }
  .card-back { left: 469px; top: 432px; }

  .accent-bar {
    position: absolute;
    background: var(--accent-blue);
  }
  .card-front .bar-left { left: 0; top: 85px; width: 22px; height: 180px; }
  .card-front .bar-right { right: 0; top: 85px; width: 21px; height: 180px; }
  .card-back .bar-left { left: 0; top: 84px; width: 22px; height: 180px; }
  .card-back .bar-divider { left: 564px; top: 84px; width: 6px; height: 180px; }

  .headline {
    position: absolute;
    font-family: "Marcellus", serif;
    color: var(--headline-white);
    white-space: nowrap;
  }
  .headline-lead { left: 48px; top: 94px; font-size: 44px; }
  .headline-key { left: 32px; top: 146px; font-size: 80px; letter-spacing: -0.5px; }

  .company-name {
    position: absolute;
    left: 44px;
    top: 30px;
    font-family: "Marcellus", serif;
    font-size: 30px;
    color: var(--headline-white);
    white-space: nowrap;
  }
  .service-list {
    position: absolute;
    left: 44px;
    top: 96px;
    width: 220px;
    list-style: none;
    font-family: "Marcellus", serif;
    font-size: 14px;
    line-height: 18px;
    color: var(--service-grey);
  }
  .service-list li {
    position: relative;
    padding-left: 14px;
    margin-bottom: 10px;
  }
  .service-list li::before {
    content: "";
    position: absolute;
    left: 0;
    top: 6px;
    width: 6px;
    height: 6px;
    background: var(--accent-blue);
  }

  .contact-block {
    position: absolute;
    right: 54px;
    top: 84px;
    text-align: right;
    font-family: "Tinos", serif;
    font-weight: 700;
    color: var(--accent-blue);
  }
  .contact-label { font-size: 29px; line-height: 32px; }
  .contact-value { font-size: 18px; line-height: 22px; margin-bottom: 12px; }
  .contact-value.name { font-size: 17px; text-transform: uppercase; letter-spacing: 0.3px; }
</style>
</head>
<body>
<main class="canvas">
  <section class="card card-front" aria-label="Card front">
    <div class="accent-bar bar-left"></div>
    <div class="accent-bar bar-right"></div>
    <p class="headline headline-lead">Are you looking for a</p>
    <p class="headline headline-key">quality service?</p>
  </section>

  <section class="card card-back" aria-label="Card back">
    <div class="accent-bar bar-left"></div>
    <div class="accent-bar bar-divider"></div>
    <p class="company-name">Flourish by Marnie T</p>
    <ul class="service-list">
      <li>Interior design for home and business</li>
      <li>Home organization and packing</li>
      <li>Staging for personal and professional space</li>
      <li>Real estate staging</li>
    </ul>
    <div class="contact-block">
      <p class="contact-label">NAME</p>
      <p class="contact-value name">Marnie T Marnie Tolvery</p>
      <p class="contact-label">Phone</p>
      <p class="contact-value">(555)687-3914</p>
      <p class="contact-label">Email</p>
      <p class="contact-value">mtbrisco@postwell.example</p>
    </div>
  </section>
</main>
</body>
</html>
```